New letter head for Air Conditioning business

We need a new professional letter head design to suit our new re-branded air conditioning business. Our new logo is attached

```html
<!DOCTYPE html>
<html lang="en">
<head>
<meta charset="utf-8">
<title>Norvane Letterhead</title>
<link rel="stylesheet" href="https://fonts.googleapis.com/css2?family=Lato:wght@400;700&family=Open+Sans:wght@400&display=swap">
<style>
  :root {
    --ink: #3a3a3c;
    --ink-soft: #4a4a4a;
    --brand-green: #5dbd7f;
    --footer-dark: #404042;
    --divider: #8b93a8;
    --paper: #ffffff;
    --sig-tone: #e4e4e4;
  }
  * { margin: 0; padding: 0; box-sizing: border-box; }
  html, body { width: 1040px; height: 1200px; overflow: hidden; background: var(--paper); }
  .letterhead {
    position: relative; width: 1040px; height: 1200px; background: var(--paper);
    font-family: "Open Sans", Arial, sans-serif; color: var(--ink-soft);
  }
  .brand {
    position: absolute; left: 104px; top: 46px; display: flex; align-items: center; gap: 18px;
  }
  .brand-dot { width: 40px; height: 40px; border-radius: 50%; background: var(--brand-green); }
  .brand-name {
    font-family: "Lato", Arial, sans-serif; font-weight: 700; font-size: 36px;
    letter-spacing: 4px; color: var(--ink);
  }
  .contact {
    position: absolute; left: 701px; top: 36px; padding-left: 20px;
    border-left: 2px solid var(--divider); height: 68px;
    font-family: "Lato", Arial, sans-serif; font-size: 18px; color: #111;
  }
  .contact-row { display: flex; align-items: center; gap: 12px; height: 22px; }
  .contact-row svg { width: 16px; height: 16px; flex: none; }
  .letter-body {
    position: absolute; left: 98px; top: 236px; width: 842px; font-size: 15px; line-height: 19px;
  }
  .issue-date { margin-bottom: 17px; }
  .recipient { margin-bottom: 50px; }
  .salutation { margin-bottom: 22px; }
  .paragraph { text-align: justify; line-height: 27px; margin-bottom: 27px; }
  .closing { margin-top: 46px; }
  .signature {
    width: 240px; height: 22px; margin: 14px 0 10px; border-radius: 3px;
    background: linear-gradient(90deg, var(--sig-tone), #f2f2f2);
  }
  .signer-name { font-size: 19px; color: var(--ink); line-height: 26px; }
  .signer-role { margin-top: 4px; }
  .footer-band { position: absolute; left: 0; top: 1030px; width: 1040px; height: 170px; }
  .footer-address {
    position: absolute; right: 89px; top: 1130px; color: #fff;
    font-family: "Lato", Arial, sans-serif; font-size: 18px;
  }
</style>
</head>
<body>
<main class="letterhead">
  <header>
    <div class="brand">
      <span class="brand-dot"></span>
      <span class="brand-name">NORVANE</span>
    </div>
    <div class="contact">
      <div class="contact-row">
        <svg viewBox="0 0 16 16"><path fill="#5dbd7f" d="M2 6c0-2 2-3 6-3s6 1 6 3l-3 1-1-2H6L5 7zM4 8h8l1 5H3z"/></svg>
        <span>044-555 010 200</span>
      </div>
      <div class="contact-row">
        <svg viewBox="0 0 16 16"><rect x="1.5" y="3.5" width="13" height="9" fill="none" stroke="#5dbd7f" stroke-width="1.6"/><path d="M1.5 3.5 8 9l6.5-5.5" fill="none" stroke="#5dbd7f" stroke-width="1.6"/></svg>
        <span>hello@norvane.example</span>
      </div>
      <div class="contact-row">
        <svg viewBox="0 0 16 16"><circle cx="8" cy="8" r="7" fill="#5dbd7f"/><path d="M5 4c2 1 1 3 3 3s1 3 3 4" stroke="#fff" stroke-width="1.4" fill="none"/></svg>
        <span>www.norvane.example</span>
      </div>
    </div>
  </header>

  <section class="letter-body">
    <p class="issue-date">Issuing Date: May 5, 2018</p>
    <p class="recipient">Name Of Employee Mr. XYZABC<br>Address of Employee<br>Address Line 2 etc..</p>
    <p class="salutation">Dear Mr.XYZABC</p>
    <p class="paragraph">Lorem Ipsum has been the industry's standard dummy text ever since the 1500s, when an unknown printer took a galley of type and scrambled it to make a type specimen book. It has survived not only five centuries, but also the leap into electronic typesetting, remaining essentially unchanged. It was popularised in the 1960s with the release of Letraset sheets containing Lorem Ipsum passages, and more recently with desktop publishing software like Aldus PageMaker including versions of Lorem Ipsum.</p>
    <p class="paragraph">Lorem Ipsum is simply dummy text of the printing and typesetting industry. Lorem Ipsum has been the industry's standard dummy text ever since the 1500s, when an unknown printer took a galley of type and scrambled it to make a type specimen book.</p>
    <p class="paragraph">It has survived not only five centuries, but also the leap into electronic typesetting, remaining essentially unchanged. It was popularised in the 1960s with the release of Letraset sheets containing Lorem IpsumIpsum passages.</p>
    <p class="closing">Yours Sincerely</p>
    <div class="signature" role="img" aria-label="Handwritten signature of Daniel Marsh"></div>
    <p class="signer-name">Daniel Marsh</p>
    <p class="signer-role">Managing Director</p>
  </section>

  <svg class="footer-band" viewBox="0 0 1040 170" preserveAspectRatio="none" aria-hidden="true">
    <path d="M0 50 C300 135 560 85 760 45 C880 25 980 20 1040 22 L1040 170 L0 170 Z" fill="var(--footer-dark)"/>
    <path d="M0 8 C180 78 420 84 624 48 C420 80 180 84 0 38 Z" fill="var(--brand-green)"/>
  </svg>
  <p class="footer-address">421, Address line here Country Name, 45452</p>
</main>
</body>
</html>
```